Website Design for Solar Panel Company

We are working with a company called VoltaNix.

Some sites to use for content/competitors and inspiration:
https://www.brivaloo.com
https://prod.aws-prod.kelmatrix.com
https://tovarqueworks.net
https://www.quorvex.com/solarpanels

Thank you for taking the time to consider designing a website for us. We are web developers based in Stockton, CA, USA. Most of our projects go through the same process. Understanding this process may help you win a project with us. We custom-code all of our websites in-house. We don’t have any requirements as to what tools you use for your design, but we prefer Figma files. For any design that we label as four-stars, we send it to the client for review. The client picks the final design they want us to use. Once we complete this process, we will continue to show additional clients all the four-star sites and purchase them later. Your designs will have multiple chances to sell. For better chances of success, we ask that you follow these guidelines.

IMAGES:
If you use any images or icons in the design, we ask that you have a link to the asset so we can purchase the image/icon. Most of the designs we submit do not have the customer’s images on them unless they have some great images. Be creative; show us the feeling you are trying to portray with your image choices. Use any royalty-free site you choose. We subscribe to Pendrel and mainly use their images, but we can purchase images outside of Pendrel. PLEASE NOTE: we will not submit designs to clients with watermarks on the images.

FONTS:
We ask that you identify the fonts used in the design. This can be done in a message if you want. We typically use Google Fonts and Pendrel Fonts.

CONTENT:
We're always open to different content and ideas. We often submit designs with stock images so the client can see our vision. We typically take pictures after the website launch to use their images with our vision. Lorem Ipsum is fine for paragraphs, but we ask that you write the headers in correct English. We want to be able to show the vision and identify the sections of the website.

INSPIRATION:
We typically add a couple of links in the brief of websites we like to help you get started in your design.

REVISIONS:
We do not often ask for revisions of the designs unless we see something in the design that may not appeal to the client. If there are slight changes that we want to make, we do that in the development process.

FEEDBACK:
We rarely give feedback on designs during the design process. We are working on many website projects and do not have the time to provide feedback. We usually respond if your request is well thought out and asks specific questions, but a note asking “feedback, please” usually goes unanswered.

```html
<!DOCTYPE html>
<html lang="en">
<head>
<meta charset="UTF-8">
<title>VoltaNix Energy Group</title>
<link href="https://fonts.googleapis.com/css2?family=Jost:wght@400;500;600;700&family=Open+Sans:wght@400;600;700&display=swap" rel="stylesheet">
<style>
:root{
  --green:#2fb21c;
  --green-bright:#3fd32a;
  --green-dark:#1b7a12;
  --black:#000;
  --ink:#0a0d0a;
  --white:#fff;
  --muted:#cfd6cf;
}
*{box-sizing:border-box;margin:0;padding:0}
html,body{width:1200px;height:3644px;overflow:hidden;background:var(--black)}
body{font-family:"Open Sans",Arial,sans-serif;color:var(--white);position:relative}
.section{position:absolute;left:0;width:1200px;overflow:hidden}
.photo{position:absolute}
.h-title{font-family:"Jost",Arial,sans-serif;font-weight:700;text-transform:uppercase;letter-spacing:1px}
.accent{color:var(--green-bright)}
.btn{display:inline-flex;align-items:center;justify-content:center;height:44px;border-radius:22px;font-family:"Jost",Arial,sans-serif;font-weight:600;font-size:16px;padding:0 30px}
.btn-green{background:linear-gradient(180deg,var(--green-bright),var(--green));color:var(--white)}
.btn-white{background:var(--white);color:var(--green-dark)}

/* hero */
.hero{top:0;height:580px}
.hero .photo{inset:0;background:linear-gradient(180deg,#1a2430 0%,#2c3a3f 35%,#3a3a30 60%,#161a14 100%)}
.hero .shade{position:absolute;inset:0;background:linear-gradient(180deg,rgba(0,0,0,.35),rgba(0,0,0,.55))}
.nav{position:absolute;top:26px;left:110px;right:100px;display:flex;align-items:center;justify-content:space-between}
.brand{display:flex;align-items:center;gap:10px;font-family:"Jost",Arial,sans-serif;font-weight:700;font-size:34px;color:var(--white);letter-spacing:1px}
.brand .dot{width:16px;height:16px;border-radius:50%;background:var(--green-bright)}
.menu{display:flex;gap:72px;font-family:"Jost",Arial,sans-serif;font-weight:600;font-size:15px;text-transform:uppercase}
.hero-body{position:absolute;top:235px;left:0;width:100%;text-align:center}
.hero-body h1{font-size:62px;line-height:1}
.hero-body p{width:780px;margin:22px auto 0;font-size:15px;line-height:1.6;color:var(--muted)}
.hero-actions{margin-top:54px;display:flex;justify-content:center;gap:26px}

/* call band */
.call{top:580px;height:230px;background:linear-gradient(180deg,#27a81a,#1f9314);text-align:center}
.call h2{font-size:50px;margin-top:42px;line-height:1.2}
.call .phone{font-family:"Jost",Arial,sans-serif;font-weight:700;font-size:54px;letter-spacing:2px;line-height:1.15}

/* about */
.about{top:810px;height:1880px;background:radial-gradient(ellipse at 70% 20%,#0f2a12 0%,#050805 55%,#000 100%)}
.about-photo{left:125px;top:130px;width:430px;height:430px;border-radius:50%;background:linear-gradient(180deg,#6fa6d8 0%,#b9d3ea 45%,#2b3f66 70%,#1b2640 100%);border:4px solid rgba(255,255,255,.15)}
.about-copy{position:absolute;left:625px;top:175px;width:470px}
.about-copy h2{font-size:50px;line-height:1}
.about-copy p{font-size:13.5px;line-height:1.75;color:var(--muted);margin-top:22px}
.about-copy p+p{margin-top:18px}
.about-copy .btn{margin-top:26px;height:36px;font-size:14px;padding:0 22px}
.video{left:115px;top:730px;width:970px;height:470px;border-radius:40px;background:linear-gradient(180deg,#3d5c86 0%,#5a6f8c 30%,#c99a5a 48%,#26344b 62%,#0f1828 100%)}
.play{position:absolute;left:565px;top:935px;width:70px;height:70px}
.est-mark{position:absolute;left:590px;top:1265px;width:20px;height:20px;border-radius:50%;border:4px solid var(--green-bright)}
.estimate{position:absolute;top:1355px;left:0;width:100%;text-align:center}
.estimate h2{font-size:50px;line-height:1}
.estimate .sub{font-size:17px;margin-top:20px}
.form{position:absolute;left:170px;top:1495px;width:860px;display:grid;grid-template-columns:1fr 1fr;column-gap:30px;row-gap:34px}
.field{height:58px;border-radius:29px;background:var(--white);color:#8a8a8a;font-size:14px;display:flex;align-items:center;justify-content:space-between;padding:0 26px}
.field svg{width:18px;height:18px}
.submit{height:64px;border-radius:32px;font-size:18px;align-self:center}

/* question */
.question{top:2670px;height:620px}
.question .photo{inset:0;background:linear-gradient(180deg,#1b2a38 0%,#2d3a3a 40%,#1c2330 70%,#0b0e12 100%)}
.question .shade{position:absolute;inset:0;background:linear-gradient(180deg,rgba(0,0,0,.3),rgba(0,0,0,.6))}
.q-body{position:absolute;top:200px;width:100%;text-align:center}
.q-body h2{font-size:50px;line-height:1}
.q-body p{width:760px;margin:22px auto 0;font-size:19px;line-height:1.6}
.q-body .hero-actions{margin-top:36px}

/* footer */
.footer{top:3290px;height:354px;background:var(--black);text-align:center}
.footer .brand{justify-content:center;margin-top:58px;font-size:44px}
.f-menu{display:flex;justify-content:center;gap:110px;margin-top:58px;font-family:"Jost",Arial,sans-serif;font-weight:600;font-size:15px;text-transform:uppercase}
.socials{display:flex;justify-content:center;gap:18px;margin-top:36px}
.socials span{width:30px;height:30px;border-radius:50%;background:var(--green)}
.copy{font-size:14px;margin-top:22px}
</style>
</head>
<body>

<section class="section hero">
  <div class="photo" role="img" aria-label="Photo of a house roof with solar panels at dusk"></div>
  <div class="shade"></div>
  <nav class="nav">
    <div class="brand"><span class="dot"></span>VOLTANIX</div>
    <div class="menu"><span>Home</span><span>About Us</span><span>Our Services</span><span>Reviews</span><span>Contact Us</span></div>
  </nav>
  <div class="hero-body">
    <h1 class="h-title">VoltaNix <span class="accent">Energy</span> Group</h1>
    <p>Sed ut perspiciatis unde omnis iste natus error sit voluptatem accusantium doloremque laudantium, totam rem aperiam, eaque ipsa quae ab illo inventore veritatis et quasi architecto.</p>
    <div class="hero-actions"><span class="btn btn-green">Get Started</span><span class="btn btn-white">Contact Us</span></div>
  </div>
</section>

<section class="section call">
  <h2 class="h-title">Call for a free evaluation</h2>
  <div class="phone">+1 888 888 8888</div>
</section>

<section class="section about">
  <div class="photo about-photo" role="img" aria-label="Photo of a technician installing rooftop solar panels"></div>
  <div class="about-copy">
    <h2 class="h-title">About <span class="accent">Us</span></h2>
    <p>At vero eos et accusamus et iusto odio dignissimos ducimus qui blanditiis praesentium voluptatum deleniti atque corrupti quos dolores et quas molestias excepturi sint occaecati cupiditate non provident, similique sunt in culpa qui officia deserunt mollitia animi, id est laborum et dolorum fuga.</p>
    <p>Et harum quidem rerum facilis est et expedita distinctio. Nam libero tempore, cum soluta nobis est eligendi optio.</p>
    <span class="btn btn-green">Read More</span>
  </div>
  <div class="photo video" role="img" aria-label="Video still of solar panels overlooking a city at dusk"></div>
  <svg class="play" viewBox="0 0 70 70"><circle cx="35" cy="35" r="35" fill="#2fb21c"/><circle cx="35" cy="35" r="24" fill="#1f8a14"/><path d="M29 24 L47 35 L29 46 Z" fill="#fff"/></svg>
  <span class="est-mark"></span>
  <div class="estimate">
    <h2 class="h-title">Request <span class="accent">an Estimate</span></h2>
    <div class="sub">Get record-breaking home solar &amp; save more</div>
  </div>
  <div class="form">
    <div class="field">First Name</div>
    <div class="field">Last Name</div>
    <div class="field">Contact Number<svg viewBox="0 0 24 24"><path d="M6 3h3l2 5-2 1.5a11 11 0 0 0 5.5 5.5L16 13l5 2v3a2 2 0 0 1-2 2A16 16 0 0 1 4 5a2 2 0 0 1 2-2z" fill="#555"/></svg></div>
    <div class="field">Email Address<svg viewBox="0 0 24 24"><rect x="3" y="5" width="18" height="14" rx="2" fill="#555"/><path d="M3 7l9 6 9-6" stroke="#fff" stroke-width="1.6" fill="none"/></svg></div>
    <div class="field">Comments<svg viewBox="0 0 24 24"><path d="M4 4h16v11H9l-5 4z" fill="#555"/></svg></div>
    <div class="btn btn-green submit">Submit Now</div>
  </div>
</section>

<section class="section question">
  <div class="photo" role="img" aria-label="Photo of a house with solar panels on the roof among trees"></div>
  <div class="shade"></div>
  <div class="q-body">
    <h2 class="h-title">Question <span class="accent">About Solar</span></h2>
    <p>Have a no obligation conversation with a solar professional privately and get answers to any questions or concerns you may have. It's that simple.</p>
    <div class="hero-actions"><span class="btn btn-green">Get Started</span><span class="btn btn-white">Contact Us</span></div>
  </div>
</section>

<footer class="section footer">
  <div class="brand"><span class="dot"></span>VOLTANIX</div>
  <div class="f-menu"><span>Home</span><span>About Us</span><span>Our Services</span><span>Reviews</span><span>Contact Us</span></div>
  <div class="socials"><span></span><span></span><span></span><span></span></div>
  <div class="copy">(C) Copyright 2024, All Rights Reserved</div>
</footer>

</body>
</html>
```